Velmor Fighting Art - Online Training

We currently have a website that we love the look and feel of at http://test.velmor.com.au/ which we are about to launch. This site is focused on face to face training we provide in private and group lessons around Australia.

We have another site we will be launching for Velmor and this one is for their online training system that will be available wordwide. The difference with this site is that it is promoting and providing access to an online training course whereas the other Velmor site you did the design for was for the face to face training they do.

The new site can be viewed at https://www.velmorfightingart.com/default.aspx (it's not live yet)

Can you please come up with a design with a similar feel to http://test.velmor.com.au/ but it also needs to be clear that it's for the online course so that people don't get confused between the two sites.

```html
<!DOCTYPE html>
<html lang="en">
<head>
<meta charset="utf-8">
<title>Velmor Fighting Art – Online Training</title>
<link href="https://fonts.googleapis.com/css2?family=Open+Sans:wght@400;600;700&family=Montserrat:wght@600;700&display=swap" rel="stylesheet">
<style>
  :root {
    --bg: #1b1b1b;
    --bg-deep: #151515;
    --gold: #d2a72c;
    --gold-dark: #b88f1d;
    --text: #e6e6e6;
    --muted: #c8c8c8;
    --white: #ffffff;
  }
  * { box-sizing: border-box; margin: 0; padding: 0; }
  html, body { width: 1200px; height: 3468px; overflow: hidden; }
  body {
    background: var(--bg);
    color: var(--text);
    font-family: "Open Sans", Arial, sans-serif;
    font-size: 15px;
    line-height: 1.6;
  }
  .benefits { height: 850px; padding: 44px 120px 0 48px; }
  .benefit { display: flex; gap: 36px; margin-bottom: 34px; }
  .benefit:nth-child(2) { margin-top: 10px; }
  .num {
    flex: 0 0 38px; height: 38px; background: var(--gold); color: var(--white);
    font-weight: 700; font-size: 17px; display: flex; align-items: center; justify-content: center;
  }
  .benefit h3 { font-size: 15px; font-weight: 700; color: var(--white); margin-bottom: 6px; }
  .benefit p { margin-bottom: 18px; color: var(--muted); }
  .rule { height: 8px; background: var(--gold); }
  .photo { width: 100%; }
  .photo-team { height: 302px; background: linear-gradient(100deg, #3f4a3a 0%, #6b6f5c 35%, #5a2a2a 55%, #3d4a36 100%); }
  .photo-drill { height: 476px; background: linear-gradient(110deg, #cfcfcf 0%, #8a8580 30%, #2f3b4a 55%, #b89a86 80%, #e0dcd6 100%); }
  .banner {
    width: 470px; height: 84px; margin: -12px auto 0; position: relative;
    background: var(--gold); color: var(--white);
    font-family: "Montserrat", Arial, sans-serif; font-weight: 700; font-size: 40px;
    display: flex; align-items: center; justify-content: center;
  }
  .teach { height: 560px; padding: 38px 200px 0; text-align: center; color: var(--muted); }
  .teach p { margin-bottom: 24px; }
  .btn {
    display: inline-block; background: var(--gold); color: var(--white);
    font-size: 14px; font-weight: 600; padding: 10px 26px; margin-top: 6px;
  }
  .why { height: 1090px; padding: 38px 120px 0 48px; }
  .why-item { display: flex; gap: 36px; margin-bottom: 26px; color: var(--muted); }
  .why-cta { text-align: center; margin-top: 18px; }
</style>
</head>
<body>
  <section class="benefits">
    <div class="benefit">
      <div class="num">6</div>
      <div>
        <h3>A Calmer Mindset</h3>
        <p>We believe that training Velmor Fighting Art helps provide more balance in your life. It better equips you to deal with other situations that may arise or better manage unforeseeable circumstances. During training you are focused, present and concentrating on your lesson with little time to think about what happened earlier that day or what will happen afterwards. You are fully immersed in your training and will begin to see amazing results in your daily life.</p>
        <p>We reinforce good behaviour and use visualisation when practicing our skill sets. Each time we practice a new skill set or technique, we are reorganising a positive pattern and discarding what no longer serves us, which ultimately helps us to create a calm and positive mindset.</p>
        <p>We believe that the journey is just as important as the destination.</p>
      </div>
    </div>
    <div class="benefit">
      <div class="num">7</div>
      <div>
        <h3>Superior Strength and Flexibility</h3>
        <p>Velmor Fighting Art helps strengthen muscle and increase balance and agility, which in turn reduces your risk of injury and enhances your quality of life. Strength, flexibility and fitness components are incorporated into training to ensure you are performing in peak condition whilst learning to defend yourself in any situation. These health and fitness benefits also translate into other sporting activities requiring speed, coordination, agility, flexibility such as rugby, tennis, football, and basketball to name a few.</p>
        <p>Studies have also shown that resistance exercise contributes to neuroplasticity and is beneficial in reorganising the brain. Strength training has also been proven to increase bone density, which is a concern as we begin to age.</p>
      </div>
    </div>
    <div class="benefit">
      <div class="num">8</div>
      <div>
        <h3>Better Overall Health</h3>
        <p>Dedicated members have reported the following benefits which include improvements to their physical well-being, as well as their emotional and mental wellbeing too!</p>
      </div>
    </div>
  </section>

  <div class="rule"></div>
  <div class="photo photo-team" role="img" aria-label="Photo of two instructors in red and black training uniforms outdoors"></div>
  <h2 class="banner">How We Teach</h2>

  <section class="teach">
    <p>We are here to guide, coach, mentor and teach you. It is more than just learning to kick and strike – it goes well beyond the physical. The skills you learn through training Velmor Fighting Art also translate into other areas of your life. As you become healthier and your overall well-being improves, your confidence and self-esteem builds and this begins to influence your behaviour at work and at home. You become more focussed at work, more attentive at home and better able to view what it's time to enjoy life. You feel a greater sense of empowerment, more confident and others will begin to notice positive changes in you as well.</p>
    <p>Regardless of where you are at in your fitness and health journey, Velmor Fighting Art training will teach you fast and effective self-defence skills, along with greater control over your body as you become fitter, stronger, more agile, flexible and adaptable.</p>
    <p>Take the first step towards your fitness and health journey today.</p>
    <a class="btn">Start Your Journey Today!</a>
  </section>

  <div class="rule"></div>
  <div class="photo photo-drill" role="img" aria-label="Photo of a student practising a self-defence block with a tattooed instructor"></div>
  <h2 class="banner">Why Us?</h2>

  <section class="why">
    <div class="why-item"><div class="num">1</div><p>Velmor Fighting Art teaches you self-defence skills that are designed to suit today's modern, urban environment. You will learn real skills that give you real results, all whilst becoming fitter, faster, stronger and more agile in every area of your life.</p></div>
    <div class="why-item"><div class="num">2</div><p>We understand that we live in a world where it's become vital to learn how to effectively protect ourselves and our loved ones. This is why we teach techniques, strategies and mindsets that will allow you to effectively and efficiently take control of any street situation.</p></div>
    <div class="why-item"><div class="num">3</div><p>You will learn to use your whole body in super-dynamic ways as your body and mind become more adaptable, flexible and agile.</p></div>
    <div class="why-item"><div class="num">4</div><p>Your self-awareness and situational awareness will heighten, allowing you to see a potential situation often before it escalates, so you can then utilise the skills you've learnt to diffuse or divert a situation before it ever becomes an incident.</p></div>
    <div class="why-item"><div class="num">5</div><p>You will learn to become fast and effective in various ranges and situations, from close quarters combat to longer range scenarios, against one or multiple attackers, and even against street weapons. You will develop skills and reflexes to strike and defend in any distance and from various angles.</p></div>
    <div class="why-item"><div class="num">6</div><p>We believe Velmor training helps provide more balance in life, and that when you're fully immersed in your training you'll begin to see amazing results and attract more positive situations and outcomes into your life.</p></div>
    <div class="why-item"><div class="num">7</div><p>Velmor is not just about kicking or striking, it goes beyond the physical. Not only do you learn practical self-defence skills, you also gain self-confidence, empowerment, focus and awareness.</p></div>
    <div class="why-item"><div class="num">8</div><p>Our online training will teach you fast and effective self defence skills that can be learnt anywhere, anytime, and at any pace.</p></div>
    <div class="why-cta"><a class="btn">Start Your Journey Today!</a></div>
  </section>
</body>
</html>
```